Coastal Learner Bureau business cards

Australian company about to start offering its services. We recruit international students to come to study English, vocational education and postgraduate courses in Australia. We help them find the institution and select the right city they want to come to Australia. We are a young, online oriented and supportive agency. Our clients are between 18 and 35 years old, mainly University students, young professionals or people with work experience. We provide much more information that any other agency offer. We administrate a Facebook group with more than 11.000 members that daily ask questions about general information when coming to Australia, while they are here and even after they leave the country

Target Market(s)

International students from South America, Central America and Europe

Industry/Entity Type

Student

Contact Information for Business Card

Tomas Bilbrea
Managing Director
tomas@kelvarin.com.au
www.kelvoria.com.au
+61 491058264
Melbourne, Australia

Font styles to use
Serif
Sans Serif

Colors

Designer to choose colors to be used in the design.

Requirements
Must have
• Horizontal design
• Standard business card size and shape. If font uses green or yellow colours, they will have to match the ones from the logo
Nice to have
• UPDATE: Use the contents of the green image to design one of the card sides. Use our logo in the background of that side as watermark.
• Passport image, or immigration stamps. A picture of the Yarra River (from Melbourne) would be cool as well.
Should not have
• Non-standard business card size and shape
• Not black as the background colour of any sides as we are not a VIP agency or a hight class service. We are orientes to young people and they like colours, pictures, something attractive.
• Vertical design
• NO YELLOW or BLACK AS THE BACKGROUND COLOUR OF ANY SIDE OF THE BIZ CARD

```html
<!DOCTYPE html>
<html lang="en">
<head>
<meta charset="utf-8">
<title>Coastal Learner Bureau business cards</title>
<link rel="stylesheet" href="https://fonts.googleapis.com/css2?family=Jost:wght@400;500;600&family=Oswald:wght@600&display=swap">
<style>
  :root {
    --paper: #efede6;
    --card-white: #ffffff;
    --brand-green: #0f6844;
    --brand-gold: #e7b925;
    --ink: #1f2a26;
    --night-top: #2a3a52;
    --night-mid: #3c4a5a;
    --night-river: #26384a;
  }
  * { box-sizing: border-box; margin: 0; padding: 0; }
  html, body { width: 1200px; height: 929px; overflow: hidden; }
  body {
    background: var(--paper);
    font-family: "Jost", sans-serif;
    display: flex;
    flex-direction: column;
    align-items: center;
    justify-content: center;
    gap: 40px;
  }
  .card {
    position: relative;
    width: 700px;
    height: 400px;
    overflow: hidden;
    box-shadow: 0 6px 18px rgba(0,0,0,0.22);
  }

  /* Front side */
  .card-front .city-photo {
    position: absolute; inset: 0;
    background:
      radial-gradient(ellipse at 38% 22%, rgba(150,130,110,0.55), transparent 45%),
      linear-gradient(180deg, var(--night-top) 0%, var(--night-mid) 50%, var(--night-river) 100%);
  }
  .card-front .brand-name {
    position: absolute;
    left: 0; right: 0; top: 140px;
    text-align: center;
    font-size: 64px;
    font-weight: 500;
    color: var(--card-white);
    letter-spacing: 1px;
  }
  .card-front .tagline {
    position: absolute;
    left: 0; right: 0; top: 270px;
    text-align: center;
    font-size: 15px;
    color: var(--card-white);
    letter-spacing: 0.5px;
  }

  /* Back side */
  .card-back { background: var(--card-white); }
  .card-back .sweep { position: absolute; inset: 0; }
  .card-back .brand-name {
    position: absolute;
    left: 44px; top: 66px;
    font-size: 40px;
    font-weight: 500;
    color: var(--brand-green);
  }
  .card-back .person {
    position: absolute;
    left: 44px; top: 160px;
  }
  .person-name {
    font-family: "Oswald", sans-serif;
    font-weight: 600;
    font-size: 34px;
    letter-spacing: 1px;
    text-transform: uppercase;
    color: var(--brand-green);
    line-height: 1.1;
  }
  .person-role {
    font-size: 20px;
    color: var(--ink);
    margin-top: 2px;
  }
  .contact-list {
    list-style: none;
    position: absolute;
    left: 44px; top: 268px;
  }
  .contact-list li {
    display: flex;
    align-items: center;
    gap: 12px;
    font-size: 17px;
    color: var(--ink);
    line-height: 27px;
    letter-spacing: 0.5px;
  }
  .contact-list svg { width: 14px; height: 14px; flex: none; }
  .contact-list .highlight { color: var(--brand-green); }
</style>
</head>
<body>

  <section class="card card-front">
    <div class="city-photo" role="img" aria-label="Evening photo of the Yarra River running through Melbourne's city skyline"></div>
    <div class="brand-name">Kelvoria</div>
    <div class="tagline">Hacemos más por ti!</div>
  </section>

  <section class="card card-back">
    <svg class="sweep" viewBox="0 0 700 400" preserveAspectRatio="none" aria-hidden="true">
      <path d="M130,0 L700,0 L700,400 L622,400 C575,180 395,40 130,0 Z" fill="var(--brand-green)"/>
      <path d="M118,10 C385,52 560,190 606,400" fill="none" stroke="var(--brand-gold)" stroke-width="8"/>
    </svg>

    <div class="brand-name">Kelvoria</div>

    <div class="person">
      <div class="person-name">Tomas Bilbrea</div>
      <div class="person-role">Managing Director</div>
    </div>

    <ul class="contact-list">
      <li>
        <svg viewBox="0 0 14 14"><rect x="3" y="1" width="8" height="12" rx="1.5" fill="none" stroke="var(--brand-green)" stroke-width="1.5"/></svg>
        +61 491058264
      </li>
      <li>
        <svg viewBox="0 0 14 14"><rect x="1" y="3" width="12" height="9" fill="var(--brand-green)"/><path d="M1,3 L7,8 L13,3" fill="none" stroke="#fff" stroke-width="1.2"/></svg>
        tomas@kelvarin.com.au
      </li>
      <li>
        <svg viewBox="0 0 14 14"><circle cx="6" cy="6" r="4" fill="none" stroke="var(--brand-green)" stroke-width="1.8"/><line x1="9" y1="9" x2="13" y2="13" stroke="var(--brand-green)" stroke-width="2"/></svg>
        <span>www.<span class="highlight">kelvoria.com.au</span></span>
      </li>
      <li>
        <svg viewBox="0 0 14 14"><path d="M7,13 C3,8 2.5,6.5 2.5,5 A4.5,4.5 0 0 1 11.5,5 C11.5,6.5 11,8 7,13 Z" fill="var(--brand-green)"/><circle cx="7" cy="5" r="1.6" fill="#fff"/></svg>
        Melbourne, Australia
      </li>
    </ul>
  </section>

</body>
</html>
```